Brainwave state designs for neurofeedback report

Design ORIGINAL graphics that correspond with existing colors and shapes for Halo Prism Grid of Stillness & Halo Prism Rhythm Panel for "Normal", "Bright Harbor", "Summit Tide" etc... patterns. You can change the shape of the white outline to be more modern looking. Perhaps you can also use white background with black outline. The frequency bars (can be more ordered) but keep the general shape of the outline.

• An original flair. Modern. Neurotechish
• Do not copy the design. Add your original ideas. Choose a font that complements the design.

```html
<!DOCTYPE html>
<html lang="en">
<head>
<meta charset="utf-8">
<title>Brainwave State Patterns</title>
<link href="https://fonts.googleapis.com/css2?family=Poppins:wght@500;600;700&display=swap" rel="stylesheet">
<style>
  :root {
    --bg: #060707;
    --ink: #ffffff;
    --glow: #1c1f1f;
    --axis: #d9d9d9;
    --band-1: #f05a2c;
    --band-2: #e6643b;
    --band-3: #f3612d;
    --band-4: #fbb83a;
    --band-5: #f4ec4f;
    --band-mid: #17492a;
    --band-low: #8696cf;
    --band-deep: #8a59a6;
    --semg: #44b549;
  }
  html, body {
    margin: 0;
    padding: 0;
    width: 1200px;
    height: 848px;
    overflow: hidden;
    background: var(--bg);
  }
  .canvas {
    display: block;
    width: 1200px;
    height: 848px;
    font-family: "Poppins", sans-serif;
  }
  .badge-disc { fill: var(--ink); }
  .badge-digit { fill: var(--bg); font-weight: 700; font-size: 37px; text-anchor: middle; }
  .band-label { fill: var(--ink); font-weight: 600; font-size: 10.5px; text-anchor: middle; }
  .band rect { rx: 3; ry: 3; }
  .outline { fill: none; stroke: var(--ink); stroke-width: 1.6; stroke-linecap: round; stroke-dasharray: 1 5; }
  .outline-trace { fill: none; stroke: var(--ink); stroke-opacity: 0.18; stroke-width: 1; }
  .node { fill: var(--bg); stroke: var(--ink); stroke-width: 1.4; }
  .axis-line { stroke: var(--axis); stroke-width: 1.4; }
  .axis-tick { stroke: var(--axis); stroke-width: 1.4; stroke-linecap: round; }
  .axis-zero { fill: var(--ink); }
  .legend-swatch { fill: var(--semg); }
  .legend-text { fill: var(--ink); font-weight: 600; font-size: 9.5px; letter-spacing: 0.6px; }
  .pattern-title { fill: var(--ink); font-weight: 600; font-size: 28px; letter-spacing: 0.4px; text-anchor: middle; }
  .b1 { fill: var(--band-1); } .b2 { fill: var(--band-2); } .b3 { fill: var(--band-3); }
  .b4 { fill: var(--band-4); } .b5 { fill: var(--band-5); }
  .bmid { fill: var(--band-mid); } .blow { fill: var(--band-low); } .bdeep { fill: var(--band-deep); }
</style>
</head>
<body>
<svg class="canvas" viewBox="0 0 1200 848" xmlns="http://www.w3.org/2000/svg">
  <defs>
    <radialGradient id="field-glow" cx="50%" cy="50%" r="50%">
      <stop offset="0%" stop-color="var(--glow)" stop-opacity="1"/>
      <stop offset="70%" stop-color="var(--glow)" stop-opacity="0.6"/>
      <stop offset="100%" stop-color="var(--bg)" stop-opacity="0"/>
    </radialGradient>
  </defs>
  <rect width="1200" height="848" fill="var(--bg)"/>

  <!-- Ordinary pattern -->
  <g class="pattern pattern-ordinary">
    <circle class="badge-disc" cx="358" cy="173" r="28"/>
    <text class="badge-digit" x="358" y="186">0</text>

    <ellipse role="img" aria-label="Soft glowing field behind the frequency bands" cx="361" cy="380" rx="150" ry="165" fill="url(#field-glow)"/>

    <g class="band">
      <rect class="b1" x="299" y="239" width="53" height="13"/><rect class="b1" x="371" y="239" width="53" height="13"/>
      <rect class="b2" x="277" y="259" width="75" height="13"/><rect class="b2" x="371" y="259" width="75" height="13"/>
      <rect class="b3" x="285" y="280" width="67" height="13"/><rect class="b3" x="371" y="280" width="67" height="13"/>
      <rect class="b4" x="291" y="300" width="61" height="13"/><rect class="b4" x="371" y="300" width="61" height="13"/>
      <rect class="b5" x="296" y="320" width="56" height="13"/><rect class="b5" x="371" y="320" width="56" height="13"/>
      <rect class="bmid" x="303" y="341" width="49" height="13"/><rect class="bmid" x="371" y="341" width="49" height="13"/>
      <rect class="bmid" x="311" y="361" width="41" height="13"/><rect class="bmid" x="371" y="361" width="41" height="13"/>
      <rect class="bmid" x="317" y="381" width="35" height="13"/><rect class="bmid" x="371" y="381" width="35" height="13"/>
      <rect class="blow" x="322" y="401" width="30" height="13"/><rect class="blow" x="371" y="401" width="30" height="13"/>
      <rect class="blow" x="320" y="422" width="32" height="13"/><rect class="blow" x="371" y="422" width="32" height="13"/>
      <rect class="blow" x="326" y="442" width="26" height="13"/><rect class="blow" x="371" y="442" width="26" height="13"/>
      <rect class="bdeep" x="328" y="462" width="24" height="13"/><rect class="bdeep" x="371" y="462" width="24" height="13"/>
      <rect class="bdeep" x="320" y="483" width="32" height="13"/><rect class="bdeep" x="371" y="483" width="32" height="13"/>
      <rect class="bdeep" x="310" y="503" width="42" height="13"/><rect class="bdeep" x="371" y="503" width="42" height="13"/>
    </g>
    <g class="band-labels">
      <text class="band-label" x="361.5" y="249.5">1</text><text class="band-label" x="361.5" y="269.5">2</text>
      <text class="band-label" x="361.5" y="290.5">3</text><text class="band-label" x="361.5" y="310.5">4</text>
      <text class="band-label" x="361.5" y="330.5">5</text><text class="band-label" x="361.5" y="351.5">6</text>
      <text class="band-label" x="361.5" y="371.5">7</text><text class="band-label" x="361.5" y="391.5">8</text>
      <text class="band-label" x="361.5" y="411.5">9</text><text class="band-label" x="361.5" y="432.5">10</text>
      <text class="band-label" x="361.5" y="452.5">11</text><text class="band-label" x="361.5" y="472.5">12</text>
      <text class="band-label" x="361.5" y="493.5">13</text><text class="band-label" x="361.5" y="513.5">14</text>
    </g>

    <path class="outline-trace" d="M236 227 C276 300 294 370 292 430 C290 475 282 500 262 527"/>
    <path class="outline-trace" d="M487 227 C447 300 429 370 431 430 C433 475 441 500 461 527"/>
    <path class="outline" d="M244 227 C283 300 302 370 300 430 C298 475 290 500 270 527"/>
    <path class="outline" d="M479 227 C440 300 421 370 423 430 C425 475 433 500 453 527"/>
    <circle class="node" cx="244" cy="227" r="3"/><circle class="node" cx="270" cy="527" r="3"/>
    <circle class="node" cx="479" cy="227" r="3"/><circle class="node" cx="453" cy="527" r="3"/>

    <g class="axis">
      <line class="axis-line" x1="173" y1="551" x2="548" y2="551"/>
      <line class="axis-tick" x1="203" y1="545" x2="203" y2="557"/><line class="axis-tick" x1="253" y1="545" x2="253" y2="557"/>
      <line class="axis-tick" x1="302" y1="545" x2="302" y2="557"/><line class="axis-tick" x1="352" y1="545" x2="352" y2="557"/>
      <line class="axis-tick" x1="370" y1="545" x2="370" y2="557"/><line class="axis-tick" x1="419" y1="545" x2="419" y2="557"/>
      <line class="axis-tick" x1="469" y1="545" x2="469" y2="557"/><line class="axis-tick" x1="518" y1="545" x2="518" y2="557"/>
      <circle class="axis-zero" cx="361" cy="551" r="2.5"/>
    </g>

    <g class="legend">
      <rect class="legend-swatch" x="303" y="586" width="32" height="19" rx="2"/>
      <text class="legend-text" x="342" y="599">sEMG</text>
      <rect class="legend-swatch" x="375" y="586" width="7" height="19" rx="2"/>
    </g>

    <text class="pattern-title" x="362" y="655">ORDINARY</text>
    <text class="pattern-title" x="362" y="688">PATTERN</text>
  </g>

  <!-- Bright Harbor pattern -->
  <g class="pattern pattern-bright-harbor">
    <circle class="badge-disc" cx="838" cy="173" r="28"/>
    <text class="badge-digit" x="838" y="186">1</text>

    <ellipse role="img" aria-label="Soft glowing field behind the frequency bands" cx="840" cy="380" rx="150" ry="165" fill="url(#field-glow)"/>

    <g class="band">
      <rect class="b1" x="798" y="239" width="32" height="13"/><rect class="b1" x="850" y="239" width="32" height="13"/>
      <rect class="b2" x="797" y="259" width="33" height="13"/><rect class="b2" x="850" y="259" width="33" height="13"/>
      <rect class="b3" x="774" y="280" width="56" height="13"/><rect class="b3" x="850" y="280" width="56" height="13"/>
      <rect class="b4" x="783" y="300" width="47" height="13"/><rect class="b4" x="850" y="300" width="47" height="13"/>
      <rect class="b5" x="772" y="320" width="58" height="13"/><rect class="b5" x="850" y="320" width="58" height="13"/>
      <rect class="bmid" x="781" y="341" width="49" height="13"/><rect class="bmid" x="850" y="341" width="49" height="13"/>
      <rect class="bmid" x="748" y="361" width="82" height="13"/><rect class="bmid" x="850" y="361" width="82" height="13"/>
      <rect class="bmid" x="789" y="381" width="41" height="13"/><rect class="bmid" x="850" y="381" width="41" height="13"/>
      <rect class="blow" x="807" y="401" width="23" height="13"/><rect class="blow" x="850" y="401" width="23" height="13"/>
      <rect class="blow" x="810" y="422" width="20" height="13"/><rect class="blow" x="850" y="422" width="20" height="13"/>
      <rect class="blow" x="792" y="442" width="38" height="13"/><rect class="blow" x="850" y="442" width="38" height="13"/>
      <rect class="bdeep" x="787" y="462" width="43" height="13"/><rect class="bdeep" x="850" y="462" width="43" height="13"/>
      <rect class="bdeep" x="771" y="483" width="59" height="13"/><rect class="bdeep" x="850" y="483" width="59" height="13"/>
      <rect class="bdeep" x="760" y="503" width="70" height="13"/><rect class="bdeep" x="850" y="503" width="70" height="13"/>
    </g>
    <g class="band-labels">
      <text class="band-label" x="840" y="249.5">1</text><text class="band-label" x="840" y="269.5">2</text>
      <text class="band-label" x="840" y="290.5">3</text><text class="band-label" x="840" y="310.5">4</text>
      <text class="band-label" x="840" y="330.5">5</text><text class="band-label" x="840" y="351.5">6</text>
      <text class="band-label" x="840" y="371.5">7</text><text class="band-label" x="840" y="391.5">8</text>
      <text class="band-label" x="840" y="411.5">9</text><text class="band-label" x="840" y="432.5">10</text>
      <text class="band-label" x="840" y="452.5">11</text><text class="band-label" x="840" y="472.5">12</text>
      <text class="band-label" x="840" y="493.5">13</text><text class="band-label" x="840" y="513.5">14</text>
    </g>

    <path class="outline-trace" d="M773 233 C750 260 742 305 742 340 C742 357 721 362 722 373 C724 387 751 390 762 399 C775 411 775 440 761 470 C750 493 737 506 726 519"/>
    <path class="outline-trace" d="M907 233 C930 260 938 305 938 340 C938 357 959 362 958 373 C956 387 929 390 918 399 C905 411 905 440 919 470 C930 493 943 506 954 519"/>
    <path class="outline" d="M780 233 C757 260 749 305 749 340 C749 357 729 362 730 373 C732 385 757 387 768 396 C782 408 782 440 768 470 C757 493 744 506 733 519"/>
    <path class="outline" d="M900 233 C923 260 931 305 931 340 C931 357 951 362 950 373 C948 385 923 387 912 396 C898 408 898 440 912 470 C923 493 936 506 947 519"/>
    <circle class="node" cx="780" cy="233" r="3"/><circle class="node" cx="733" cy="519" r="3"/>
    <circle class="node" cx="900" cy="233" r="3"/><circle class="node" cx="947" cy="519" r="3"/>
    <circle class="node" cx="730" cy="373" r="3"/><circle class="node" cx="950" cy="373" r="3"/>

    <g class="axis">
      <line class="axis-line" x1="652" y1="551" x2="1027" y2="551"/>
      <line class="axis-tick" x1="682" y1="545" x2="682" y2="557"/><line class="axis-tick" x1="732" y1="545" x2="732" y2="557"/>
      <line class="axis-tick" x1="781" y1="545" x2="781" y2="557"/><line class="axis-tick" x1="831" y1="545" x2="831" y2="557"/>
      <line class="axis-tick" x1="849" y1="545" x2="849" y2="557"/><line class="axis-tick" x1="899" y1="545" x2="899" y2="557"/>
      <line class="axis-tick" x1="948" y1="545" x2="948" y2="557"/><line class="axis-tick" x1="998" y1="545" x2="998" y2="557"/>
      <circle class="axis-zero" cx="840" cy="551" r="2.5"/>
    </g>

    <g class="legend">
      <rect class="legend-swatch" x="783" y="586" width="32" height="19" rx="2"/>
      <text class="legend-text" x="822" y="599">sEMG</text>
      <rect class="legend-swatch" x="855" y="586" width="7" height="19" rx="2"/>
    </g>

    <text class="pattern-title" x="842" y="655">BRIGHT HARBOR</text>
    <text class="pattern-title" x="842" y="688">PATTERN</text>
  </g>
</svg>
</body>
</html>
```